Business Card for a Dental Office

The design should communicate integrity, quality and reliability. We also want the card look elegant, simple, but still stand out, different from the traditional-dental-office business card.

Industry/Entity Type

Business

```html
<!DOCTYPE html>
<html lang="en">
<head>
<meta charset="utf-8">
<title>Harlow Dental Studio — Business Card</title>
<link rel="stylesheet" href="https://fonts.googleapis.com/css2?family=Bebas+Neue&family=Source+Sans+3:wght@400;600&display=swap">
<style>
  :root {
    --stage-top: #2b2b2b;
    --stage-bottom: #050505;
    --card-white: #ffffff;
    --card-mist: #f1f2f4;
    --gold: #d6bf2c;
    --gold-deep: #c8ae24;
    --gold-text: #c9ab1c;
    --ink: #111111;
    --body-ink: #2e2e2e;
    --on-gold: #ffffff;
  }
  * { box-sizing: border-box; margin: 0; padding: 0; }
  html, body {
    width: 1200px;
    height: 900px;
    overflow: hidden;
  }
  body {
    background: linear-gradient(180deg, var(--stage-top) 0%, #141414 60%, var(--stage-bottom) 100%);
    font-family: "Source Sans 3", "Myriad Pro", Arial, sans-serif;
    position: relative;
  }
  .card {
    position: absolute;
    top: 184px;
    width: 302px;
    height: 491px;
    border-radius: 13px;
    overflow: hidden;
    text-align: center;
  }
  .card--front {
    left: 299px;
    background: linear-gradient(180deg, var(--card-white) 0%, var(--card-white) 35%, var(--card-mist) 100%);
  }
  .card--back {
    left: 646px;
    background: linear-gradient(180deg, var(--gold) 0%, #dbc632 60%, var(--gold-deep) 100%);
  }
  .brand-mark {
    position: absolute;
    left: 131px;
    top: 238px;
    width: 40px;
    height: 40px;
    background: var(--gold);
  }
  .card--front .brand-mark { top: 54px; }
  .brand-name {
    position: absolute;
    left: 0;
    width: 100%;
    font-family: "Bebas Neue", "Oswald", sans-serif;
    font-weight: 400;
    font-size: 35px;
    line-height: 1;
    letter-spacing: 0.2px;
  }
  .tagline {
    position: absolute;
    left: 0;
    width: 100%;
    font-size: 12.5px;
    font-weight: 600;
    letter-spacing: 0.9px;
    line-height: 1;
    text-transform: uppercase;
  }
  .card--front .brand-name { top: 150px; color: var(--ink); }
  .card--front .tagline { top: 179px; color: var(--gold-text); }
  .card--back .brand-name { top: 407px; color: var(--on-gold); }
  .card--back .tagline { top: 437px; color: var(--on-gold); }

  .person-name {
    position: absolute;
    top: 268px;
    left: 0; width: 100%;
    font-size: 20px;
    font-weight: 600;
    color: var(--gold-text);
    letter-spacing: 0.3px;
  }
  .person-role {
    position: absolute;
    top: 293px;
    left: 0; width: 100%;
    font-size: 15px;
    color: var(--body-ink);
  }
  .contact-list {
    position: absolute;
    top: 342px;
    left: 0; width: 100%;
    list-style: none;
    font-size: 14.5px;
    color: var(--body-ink);
    line-height: 20px;
  }
  .contact-list li { display: flex; justify-content: center; align-items: center; gap: 8px; }
  .contact-list svg { width: 10px; height: 10px; fill: var(--gold-text); }
  .address {
    position: absolute;
    top: 420px;
    left: 0; width: 100%;
    font-size: 14.5px;
    line-height: 16.5px;
    color: var(--body-ink);
    font-style: normal;
  }
</style>
</head>
<body>
  <section class="card card--front" aria-label="Card front">
    <span class="brand-mark" aria-hidden="true"></span>
    <h1 class="brand-name">Harlow Dental Studio</h1>
    <p class="tagline">Your smile is your gift to others</p>

    <h2 class="person-name">JOHN SMITH</h2>
    <p class="person-role">Managing Direcator</p>

    <ul class="contact-list">
      <li>
        <svg viewBox="0 0 10 10" aria-hidden="true"><path d="M1 4 C1 1.5 9 1.5 9 4 L7.5 4.6 L7 3.6 L3 3.6 L2.5 4.6 Z M2.5 5.2 L7.5 5.2 L8.5 9 L1.5 9 Z"/></svg>
        <span>823-456-7890</span>
      </li>
      <li>
        <svg viewBox="0 0 10 10" aria-hidden="true"><path d="M0.5 2 H9.5 V8.5 H0.5 Z" /><path d="M0.5 2 L5 5.5 L9.5 2" fill="none" stroke="#ffffff" stroke-width="0.9"/></svg>
        <span>info@youremail.com</span>
      </li>
    </ul>

    <address class="address">1234, Address Goes Here<br>Country Name, 123456</address>
  </section>

  <section class="card card--back" aria-label="Card back">
    <h2 class="brand-name">Harlow Dental Studio</h2>
    <p class="tagline">Your smile is your gift to others</p>
  </section>
</body>
</html>
```